Mastering Modern Vineyard Management

size of the ad - 8”x 10.75" plus 0.25" bleed
I would like an ad for a magazine that will stand out and make people want to read the ad.
The ad should not be crowded and people reading the ad will be able to read the text.
I would like it to be a creative and modern-day design.
the list of topics should not be the focus of the ad.
the text is attached.
If you decide to use people in the ad then please no ladies.
please note that leave over 1 inch for the bottom of the footer

```html
<!DOCTYPE html>
<html lang="en">
<head>
<meta charset="utf-8">
<title>Mastering Modern Vineyard Management – Magazine Ad</title>
<link rel="stylesheet" href="https://fonts.googleapis.com/css2?family=Bebas+Neue&family=Kaushan+Script&family=Roboto:wght@500&display=swap">
<style>
  :root {
    --stage: #e4e4e4;
    --page: #121212;
    --ink: #ffffff;
    --ink-soft: #dcdcdc;
    --accent: #e01b1b;
    --sky-top: #c9d6e3;
    --sky-mid: #6f8aa6;
    --tower-dark: #1a2332;
  }
  * { margin: 0; padding: 0; box-sizing: border-box; }
  html, body {
    width: 1200px; height: 818px; overflow: hidden;
    background: var(--stage);
  }
  .ad-page {
    position: absolute; left: 314px; top: 0;
    width: 572px; height: 818px;
    background: var(--page);
    color: var(--ink);
    font-family: "Bebas Neue", sans-serif;
  }
  .ad-header {
    position: absolute; left: 75px; top: 24px;
    width: 290px; height: 46px;
    display: flex; align-items: center; gap: 12px;
  }
  .ad-header__title {
    font-size: 22px; line-height: 21px; letter-spacing: 0.5px;
    white-space: nowrap;
  }
  .ad-header__script {
    font-family: "Kaushan Script", cursive;
    font-size: 28px; line-height: 1; white-space: nowrap;
  }
  .ad-header__cap { position: absolute; left: 380px; top: 24px; }
  .hero-photo {
    position: absolute; left: 75px; top: 79px;
    width: 422px; height: 469px;
    background:
      linear-gradient(200deg, transparent 55%, rgba(18,18,18,0.85) 100%),
      linear-gradient(160deg, var(--sky-top) 0%, var(--sky-mid) 40%, var(--tower-dark) 85%);
  }
  .schedule {
    position: absolute; left: 90px; top: 408px;
    font-size: 37px; line-height: 42px; letter-spacing: 0.3px;
  }
  .schedule__days { color: var(--accent); }
  .side-note {
    position: absolute; left: 530px; top: 337px;
    transform: translate(-50%, -50%) rotate(-90deg);
    font-family: "Roboto", sans-serif; font-weight: 500;
    font-size: 10px; letter-spacing: 2.6px; white-space: nowrap;
    color: var(--ink-soft);
  }
  .offer {
    position: absolute; left: 0; right: 0; top: 594px;
    text-align: center; font-size: 23px; line-height: 29px;
    letter-spacing: 0.8px; color: var(--ink-soft);
  }
  .topics {
    position: absolute; left: 0; right: 0; top: 676px;
    text-align: center;
    font-family: "Roboto", sans-serif; font-weight: 500;
    font-size: 9.6px; line-height: 17px; letter-spacing: 0.5px;
    color: var(--ink-soft);
  }
  .topics__sep { margin: 0 4px; }
</style>
</head>
<body>
  <main class="ad-page">
    <header class="ad-header">
      <span class="ad-header__title">Mastering Modern<br>Vineyard Management</span>
      <span class="ad-header__script">Course</span>
    </header>
    <svg class="ad-header__cap" width="86" height="48" viewBox="0 0 86 48" aria-hidden="true">
      <polygon points="43,2 84,16 43,30 2,16" fill="var(--accent)"/>
      <path d="M20 22 V38 Q43 48 66 38 V22 L43 30 Z" fill="var(--accent)"/>
      <line x1="6" y1="17" x2="6" y2="40" stroke="var(--accent)" stroke-width="2"/>
      <rect x="3" y="38" width="6" height="7" fill="var(--accent)"/>
    </svg>

    <div class="hero-photo" role="img" aria-label="Upward view of tall glass buildings against a pale blue sky"></div>

    <div class="schedule">
      <div>Starting Feb.28</div>
      <div class="schedule__days">Monday 10 AM - Tuesday</div>
      <div>Evenings Sessions</div>
    </div>

    <div class="side-note">LIMITED PARTIAL SCHOLARSHIPS</div>

    <p class="offer">Early bird special for those that<br>started or would like to go into vineyards</p>

    <p class="topics">
      Site selection<span class="topics__sep">|</span>Vineyard investment strategies<span class="topics__sep">|</span>Due diligence<br>
      Financing<span class="topics__sep">|</span>Canopy management<span class="topics__sep">|</span>Vineyard operations<span class="topics__sep">|</span>Wine law basics<br>
      Sourcing vines<span class="topics__sep">|</span>Irrigation<span class="topics__sep">|</span>Dealing with wineries<span class="topics__sep">|</span>Tax fundamentals
    </p>
  </main>
</body>
</html>
```